brqnal new business card design project

we need a new business card design. you can view info about us @ brqnal-example.com. i have attached an example of our previous card with our previous name that we no longer use. We really liked the design, colors etc. look below to see more info about this project. it asks for a limited number of words. please see our website for more info about our compnay.

Target Market(s)

law enforcement

Contact Information for Business Card

i have uploaded an example of what we used before that we liked.

Font styles to use
Serif

```html
<!DOCTYPE html>
<html lang="en">
<head>
<meta charset="utf-8">
<title>brqnal business card</title>
<link rel="stylesheet" href="https://fonts.googleapis.com/css2?family=Cormorant+Garamond:wght@300;400&family=Source+Serif+4:ital,wght@0,400;1,400&display=swap">
<style>
  :root {
    --backdrop: #d9d9d9;
    --navy: #0b1620;
    --navy-deep: #08121b;
    --blue: #0f72b5;
    --white: #ffffff;
    --paper: #f2f2f2;
    --ink: #2a3038;
    --muted: #c7ccd2;
  }
  * { margin: 0; padding: 0; box-sizing: border-box; }
  html, body { width: 1200px; height: 576px; overflow: hidden; background: var(--backdrop); }
  .canvas { position: relative; width: 1200px; height: 576px; }
  .card {
    position: absolute; top: 138px; width: 484px; height: 293px;
    border-radius: 13px; overflow: hidden; background: var(--navy);
  }
  .card--front { left: 82px; }
  .card--back { left: 602px; width: 481px; height: 291px; background: var(--paper); }

  .network-map {
    position: absolute; left: 24px; top: 20px; width: 430px; height: 240px;
    background: radial-gradient(ellipse at 50% 50%, rgba(40,80,100,0.35), rgba(11,22,32,0) 70%);
  }
  .wordmark {
    position: absolute; font-family: "Cormorant Garamond", serif; font-weight: 300;
    color: var(--white); letter-spacing: 3px; white-space: nowrap; line-height: 1;
  }
  .card--front .wordmark { left: 0; right: 0; top: 94px; text-align: center; font-size: 66px; }
  .front-stripes { position: absolute; left: 0; bottom: 0; }
  .front-url {
    position: absolute; right: 24px; bottom: 9px;
    font-family: "Source Serif 4", serif; font-size: 11.5px; letter-spacing: 1.2px; color: var(--muted);
  }

  .back-panel { position: absolute; left: 0; top: 0; }
  .card--back .wordmark { left: 0; width: 256px; top: 110px; text-align: center; font-size: 46px; letter-spacing: 2px; }
  .tagline {
    position: absolute; left: 0; width: 256px; top: 158px; text-align: center;
    font-family: "Source Serif 4", serif; font-size: 9.5px; letter-spacing: 0.6px; color: var(--muted); white-space: nowrap;
  }
  .tagline .divider { color: var(--blue); margin: 0 5px; }

  .contact { position: absolute; left: 300px; top: 74px; font-family: "Source Serif 4", serif; color: var(--ink); }
  .contact__name { font-size: 21px; color: var(--blue); line-height: 1.2; }
  .contact__title { font-size: 12px; font-style: italic; margin-top: 2px; }
  .contact__address { font-size: 12.5px; line-height: 17px; margin-top: 15px; }
  .contact__lines { list-style: none; margin-top: 7px; font-size: 12.5px; line-height: 17px; }
  .contact__lines li { display: flex; align-items: center; white-space: nowrap; }
  .contact__lines svg { width: 10px; height: 10px; margin: 0 11px 0 4px; fill: var(--blue); flex: none; }
</style>
</head>
<body>
<main class="canvas">

  <section class="card card--front" aria-label="Card front">
    <div class="network-map" role="img" aria-label="Faint network map of the country with connected points"></div>
    <div class="wordmark">BRQNAL</div>
    <svg class="front-stripes" width="484" height="30" viewBox="0 0 484 30" aria-hidden="true">
      <polygon points="0,6 193,6 182,30 0,30" fill="var(--blue)"/>
      <polygon points="210,6 270,6 258,30 198,30" fill="var(--white)"/>
    </svg>
    <div class="front-url">www.brqnal-example.com</div>
  </section>

  <section class="card card--back" aria-label="Card back">
    <svg class="back-panel" width="481" height="291" viewBox="0 0 481 291" aria-hidden="true">
      <path d="M0,0 H215 C250,60 275,160 245,291 H0 Z" fill="var(--blue)"/>
      <path d="M0,0 H207 C240,60 264,160 236,291 H0 Z" fill="var(--navy-deep)"/>
    </svg>
    <div class="wordmark">BRQNAL</div>
    <div class="tagline">Better Technology<span class="divider">|</span>Better Service</div>

    <div class="contact">
      <div class="contact__name">Daniel Marsh</div>
      <div class="contact__title">Founder/Chief Exe. Officer</div>
      <div class="contact__address">4120 Ridgeline Avenue<br>Austin, TX 78701</div>
      <ul class="contact__lines">
        <li><svg viewBox="0 0 10 10"><path d="M1,3 Q5,0 9,3 L8,4.5 L6.5,4 V3 H3.5 V4 L2,4.5 Z M2,5.5 H8 L9,9 H1 Z"/></svg>555.014.2290</li>
        <li><svg viewBox="0 0 10 10"><path d="M0,2 H10 V8 H0 Z M0.8,2.6 L5,5.6 L9.2,2.6" stroke="var(--paper)" stroke-width="0.8"/></svg>info@brqnal-example.com</li>
        <li><svg viewBox="0 0 10 10"><circle cx="5" cy="5" r="4.5"/><path d="M0.5,5 H9.5 M5,0.5 V9.5 M2,2.5 Q5,4 8,2.5 M2,7.5 Q5,6 8,7.5" stroke="var(--paper)" stroke-width="0.7" fill="none"/></svg>www.brqnal-example.com</li>
      </ul>
    </div>
  </section>

</main>
</body>
</html>
```